Local massage therapist needs some new marketing material

Hi there! I am a massage therapist here in Denver, CO in Alder Bend(shopping and art district) of the city. My business is called Lumo Bodywork of Denver. My practice has an eastern influence and I do reflexology, thai massage and use Chinese herbs, etc. I know all my clients and pay close attention to details. I am also very respectful of tradition and it shows in how I work. I tend to like modern, clean, fun, Asian designs. I am wanting a new business card and brochure. I have a logo and branding for my business that I want used in the design. Currently, the sign for my building is purple and I think my logo was designed to be purple. I will attach pictures of it and can send whatever files are necessary so it can be integrated into the brochure, etc. I like the purple but open to using other colors as well. Thanks!
My website is lumobodyworkofdenver.example where info can be gathered about me and services/fees for brochure.
Updates

Just increased budget. Please see new feedback in discussion thread.

Thanks!

                                       HEY ALL,

Just wanted to let you know that I made a change to my website. It is on the Prices Page. I no longer have the frequent  flyer prices but I added discounts. Let me know if you have any questions. Thanks so much!

Target Market(s)

healthy, urban, educated, upper middle class, yogis

Industry/Entity Type

Marketing

Requirements
Must have
• logo stays purple
Should not have
• not too busy

```html
<!DOCTYPE html>
<html lang="en">
<head>
<meta charset="utf-8">
<title>Lumo Bodywork – Business Card</title>
<link href="https://fonts.googleapis.com/css2?family=Source+Sans+3:ital,wght@0,400;0,600;0,700;1,400&display=swap" rel="stylesheet">
<style>
  :root {
    --purple: #662d91;
    --charcoal: #3a3a3a;
    --ink: #3d3d3d;
    --muted: #6a6a6a;
    --rule: #9a9a9a;
    --paper: #ffffff;
    --backdrop: #ebebef;
  }
  * { box-sizing: border-box; margin: 0; padding: 0; }
  html, body {
    width: 1200px; height: 987px; overflow: hidden;
    background: var(--backdrop);
    font-family: "Source Sans 3", "Myriad Pro", Arial, sans-serif;
    color: var(--ink);
  }
  .card {
    position: absolute; left: 232px;
    width: 735px; height: 420px;
    background: var(--paper);
    border-radius: 34px;
    overflow: hidden;
    box-shadow: 0 6px 22px rgba(0,0,0,0.12);
  }
  .card--front { top: 40px; }
  .card--back { top: 527px; }

  /* Front */
  .swoosh { position: absolute; inset: 0; width: 100%; height: 100%; }
  .brand {
    position: absolute; left: 40px; top: 62px; width: 270px;
    display: flex; flex-direction: column; align-items: center;
  }
  .brand__dot {
    width: 54px; height: 54px; border-radius: 50%;
    background: var(--purple);
    margin-bottom: 8px;
  }
  .brand__name {
    font-size: 84px; font-weight: 400; line-height: 1;
    letter-spacing: 8px; color: var(--purple);
  }
  .divider {
    position: absolute; left: 330px; top: 110px;
    width: 1.5px; height: 200px; background: var(--rule);
  }
  .contact { position: absolute; left: 354px; top: 110px; }
  .contact__name { font-size: 30px; font-weight: 700; color: var(--purple); line-height: 1; }
  .contact__title { font-size: 19px; margin-top: 2px; margin-bottom: 16px; }
  .contact__line { display: flex; align-items: center; gap: 8px; font-size: 19px; line-height: 1.4; }
  .contact__line svg { width: 15px; height: 15px; flex: none; }
  .contact__address { font-size: 19px; margin-top: 6px; margin-left: -4px; }

  /* Back */
  .appt { position: absolute; left: 60px; top: 40px; right: 60px; }
  .appt__heading {
    text-align: center; font-size: 20px; font-weight: 700;
    color: var(--purple); letter-spacing: 0.5px; margin-left: 60px;
  }
  .appt__field { display: flex; align-items: flex-end; gap: 10px; font-size: 19px; margin-top: 14px; }
  .appt__blank { flex: 1; border-bottom: 1px dotted #777; height: 1px; margin-bottom: 5px; }
  .appt__time { margin-left: 150px; margin-top: 30px; }
  .appt__hours { font-size: 22px; line-height: 1.3; margin-top: 34px; text-align: center; }
  .appt__note { font-size: 19px; font-style: italic; color: var(--muted); text-align: center; margin-top: 22px; }
</style>
</head>
<body>

<section class="card card--front" aria-label="Business card front">
  <svg class="swoosh" viewBox="0 0 735 420" preserveAspectRatio="none" aria-hidden="true">
    <path d="M0 232 C170 285 400 370 600 420 L0 420 Z" fill="var(--charcoal)"/>
    <path d="M0 262 C160 312 370 386 520 420 L0 420 Z" fill="var(--paper)"/>
    <path d="M0 270 C160 320 360 390 500 420 L0 420 Z" fill="var(--purple)"/>
    <path d="M0 380 C120 394 250 410 330 420 L0 420 Z" fill="var(--charcoal)"/>
  </svg>

  <div class="brand">
    <div class="brand__dot"></div>
    <div class="brand__name">LUMO</div>
  </div>

  <div class="divider"></div>

  <div class="contact">
    <div class="contact__name">Your Name</div>
    <div class="contact__title">Title</div>
    <div class="contact__line">
      <svg viewBox="0 0 16 16" aria-hidden="true"><circle cx="8" cy="8" r="8" fill="var(--purple)"/><path d="M5 4.5 L7 4.3 L7.6 6.4 L6.6 7.2 C7 8.2 7.8 9 8.8 9.4 L9.6 8.4 L11.7 9 L11.5 11 C8 11.4 4.6 8 5 4.5 Z" fill="#fff"/></svg>
      555.201.0148
    </div>
    <div class="contact__line">
      <svg viewBox="0 0 16 16" aria-hidden="true"><circle cx="8" cy="8" r="8" fill="var(--purple)"/><rect x="3.5" y="5" width="9" height="6" fill="#fff"/><path d="M3.5 5 L8 8.5 L12.5 5" stroke="var(--purple)" stroke-width="1" fill="none"/></svg>
      info@lumobodyworkofdenver.example
    </div>
    <div class="contact__line">
      <svg viewBox="0 0 16 16" aria-hidden="true"><circle cx="8" cy="8" r="8" fill="var(--purple)"/><circle cx="8" cy="8" r="4.5" stroke="#fff" stroke-width="1" fill="none"/><ellipse cx="8" cy="8" rx="2" ry="4.5" stroke="#fff" stroke-width="1" fill="none"/><line x1="3.5" y1="8" x2="12.5" y2="8" stroke="#fff" stroke-width="1"/></svg>
      www.lumobodyworkofdenver.example
    </div>
    <div class="contact__address">1450 Alder Ave, Larkfield, CO 81999</div>
  </div>
</section>

<section class="card card--back" aria-label="Business card back">
  <div class="appt">
    <div class="appt__heading">YOUR APPOINTMENT</div>
    <div class="appt__field"><span>Name :</span><span class="appt__blank"></span></div>
    <div class="appt__field"><span>Date :</span><span class="appt__blank"></span></div>
    <div class="appt__field appt__time"><span>Time :</span><span class="appt__blank"></span><span>am / pm</span></div>
    <p class="appt__hours">Tues - Fri 9am - 7pm Sat 9am-4pm<br>(Appointments required) No walk-ins please.</p>
    <p class="appt__note">We appreciate a 24 hr. notice for cancellations</p>
  </div>
</section>

</body>
</html>
```